VOR Exterior Coatings

double sided. the front i want the name of the business each word on a new line with the VOR being bigger. id like teal, black and white colors. the back i want my contact info. Flat, no gloss. Something professional and I want to feel the letters bump put of the card. if possible maybe a paint sprayer in corner. not a car paint spray. (no tank on top of gun)
no vehicle paint sprayers. that means no tank on top of the gun. doesn't have to have a sprayer. black/dark background on the front. white back ground on back with info

```html
<!DOCTYPE html>
<html lang="en">
<head>
<meta charset="utf-8">
<title>VOR Exterior Coatings – Business Card</title>
<link href="https://fonts.googleapis.com/css2?family=Lato:wght@400;900&family=Oswald:wght@600&display=swap" rel="stylesheet">
<style>
  :root {
    --bg: #6c6c6c;
    --paper: #f4f4f5;
    --teal: #016b6c;
    --aqua: #17d9e0;
    --ink: #4a4a4a;
    --rule: #5a5a5a;
  }
  * { box-sizing: border-box; margin: 0; padding: 0; }
  html, body { width: 1200px; height: 800px; overflow: hidden; }
  body {
    background: var(--bg);
    display: flex;
    align-items: center;
    justify-content: center;
    gap: 40px;
    font-family: "Lato", Arial, sans-serif;
  }
  .card {
    width: 540px;
    height: 309px;
    flex: none;
    box-shadow: 0 6px 18px rgba(0,0,0,.25);
  }
  /* Contact side */
  .card--contact {
    background: var(--paper);
    display: flex;
    align-items: center;
    justify-content: center;
    gap: 22px;
  }
  .identity {
    text-align: right;
    color: var(--ink);
    font-size: 14px;
    line-height: 1.35;
  }
  .identity__name {
    font-family: "Oswald", "Arial Narrow", sans-serif;
    font-weight: 600;
    color: var(--teal);
    font-size: 24px;
    letter-spacing: .5px;
    line-height: 1.1;
    text-transform: uppercase;
  }
  .identity__title { margin-bottom: 6px; }
  .divider {
    width: 1px;
    height: 100px;
    background: var(--rule);
  }
  .contact-list {
    list-style: none;
    color: var(--ink);
    font-size: 14px;
    line-height: 1.45;
  }
  .contact-list li {
    display: flex;
    align-items: center;
    gap: 8px;
  }
  .contact-list svg {
    width: 12px;
    height: 12px;
    fill: var(--teal);
    flex: none;
  }
  /* Brand side */
  .card--brand {
    background: var(--teal);
    display: flex;
    align-items: center;
    justify-content: center;
  }
  .brand-name {
    font-family: "Lato", Arial, sans-serif;
    font-weight: 900;
    color: var(--aqua);
    text-transform: uppercase;
    text-align: center;
    line-height: 1;
  }
  .brand-name__main {
    display: block;
    font-size: 96px;
    letter-spacing: 4px;
    margin-bottom: 8px;
  }
  .brand-name__word {
    display: block;
    font-size: 24px;
    letter-spacing: 4px;
    line-height: 1.2;
  }
</style>
</head>
<body>

  <section class="card card--contact" aria-label="Contact side">
    <div class="identity">
      <h1 class="identity__name">Daniel Morrow</h1>
      <p class="identity__title">Founder &amp; CEO</p>
      <p>4120 Birchwood Court</p>
      <p>Fairhaven, Alaska 99507</p>
    </div>
    <div class="divider"></div>
    <ul class="contact-list">
      <li>
        <svg viewBox="0 0 12 12" aria-hidden="true"><path d="M2.5 1h2l1 3-1.5 1a6 6 0 0 0 3 3l1-1.5 3 1v2a1 1 0 0 1-1 1A9 9 0 0 1 1.5 2a1 1 0 0 1 1-1z"/></svg>
        555-201-4837
      </li>
      <li>
        <svg viewBox="0 0 12 12" aria-hidden="true"><path d="M3 0h6a1 1 0 0 1 1 1v10a1 1 0 0 1-1 1H3a1 1 0 0 1-1-1V1a1 1 0 0 1 1-1zm.5 1.5v8h5v-8z"/></svg>
        555-201-4838
      </li>
      <li>
        <svg viewBox="0 0 12 12" aria-hidden="true"><path d="M3 0h6v3H3zM1 4h10a1 1 0 0 1 1 1v4H10v3H2V9H0V5a1 1 0 0 1 1-1zm2 4v3h6V8z"/></svg>
        555-201-4839
      </li>
      <li>
        <svg viewBox="0 0 12 12" aria-hidden="true"><path d="M0 2h12v8H0zm1 1v.4l5 3.2 5-3.2V3z"/></svg>
        info@vorexteriorcoatings.com
      </li>
      <li>
        <svg viewBox="0 0 12 12" aria-hidden="true"><circle cx="6" cy="6" r="6"/><path d="M1 6h10M6 1v10" stroke="#f4f4f5" stroke-width="1"/></svg>
        www.vorexteriorcoatings.com
      </li>
    </ul>
  </section>

  <section class="card card--brand" aria-label="Brand side">
    <p class="brand-name">
      <span class="brand-name__main">VOR</span>
      <span class="brand-name__word">Exterior</span>
      <span class="brand-name__word">Coatings</span>
    </p>
  </section>

</body>
</html>
```